RIVERSTONE PULSE GYM FLYER DESIGN

We want a flyer designed for our gym. We have an example of a flyer which we like and I have put it into the images I have uploaded. I would like to recreate using our pictures, so its a pretty straight forward job. We also want to put our weekly timetable on the back of the flyer. We would like the size of the flyer to be A5.

Target Market(s)

FITNESS

Industry/Entity Type

Gym

Colors
33a6d7
ffffff

Requirements
Must have
• We just want to recreate the flyer but we must have the following info on the flyer and we want our timetable on the back of the flyer which you can get from this link: http://www.riverstonepulsegym-example.com/timetable
• Riverstone Pulse Gym is a fun community of humble people. Our goal is to help guide you towards a fitter, healthier lifestyle!
• Our Programs
• HIIT
• High intensity interval training is 30-45 minutes of fat burning fun. The class is a mix of cardio, bodyweight and some resistance movements.
• Conditioning
• A full hour of strength, cardio and bodyweight training to get you in tip top shape. Expect a mix of barbells, kettlebells, rowing machines, bikes and other training methods.
• BWS
• This is our big Friday session to set you up for the weekend. 90 minutes of hard training that is done with a team emphasis. From heavy lifting to cardio triathlons, this class has it all but not for the faint hearted.
• Muay Thai
• Commonly known as the science of 8 limbs you will learn how to punch, kick, knee and elbow. Thailands national sport is a great way to get your fitness kick. We train the complete beginner all the way to international fighters so you are in great hands.
• Kids Muay Thai
• Our junior program starts from age 6 onwards. Muay Thai is a great way for kids to get active and fit while learning new skills. Training in martial arts also teaches self discipline and socialisation skills.
• Yoga
• A combination of physical and mental practises that will leave you focused and refreshed for whatever the week throws at you. We always recommend our yoga classes as a great way to balance the high intensity training we offer.
• Q-Press
• Strength training with a little bit of conditioning. We regularly update the program and re test lifts to ensure you are making progress and getting stronger.
• CONTACT US
• OUR LOCATION:
• Unit 27C
• 214 Kelvane Road
• Marrow Heath
• Glasgow
• G72QT
• Phone: 07930625184
• Email: info@riverstonepulsegym-example.com
• Web: www.riverstonepulsegym-example.com
Nice to have
• Can use all the picture but if not be good to use the boxing one and the group training one.

```html
<!DOCTYPE html>
<html lang="en">
<head>
<meta charset="utf-8">
<title>Riverstone Pulse Gym Flyer</title>
<link href="https://fonts.googleapis.com/css2?family=Oswald:wght@300;400&family=Roboto+Condensed:wght@400;700&family=Open+Sans:wght@400;600;700&display=swap" rel="stylesheet">
<style>
:root{
  --blue:#14a6e2;
  --blue-dark:#0b8ccd;
  --blue-light:#4cc3f0;
  --blue-cell:#1aa8e4;
  --pink:#e6197f;
  --white:#ffffff;
  --ink:#10161d;
  --page:#e8ebee;
  --band:#dcdfe2;
}
*{margin:0;padding:0;box-sizing:border-box}
html,body{width:824px;height:1200px;overflow:hidden;background:var(--page)}
.canvas{position:relative;width:824px;height:1200px;overflow:hidden}

/* FRONT */
.front{position:absolute;left:0;top:10px;width:824px;height:580px;overflow:hidden;background:var(--blue);font-family:"Roboto Condensed",sans-serif;color:var(--white)}
.front-shapes{position:absolute;left:0;top:0}
.headline{position:absolute;left:24px;top:16px;font-family:"Oswald",sans-serif;font-weight:400;font-size:35px;line-height:40px;letter-spacing:-0.5px}
.intro{position:absolute;left:20px;top:140px;width:235px;text-align:center;font-size:12.5px;line-height:17px;letter-spacing:-0.3px}
.intro p+p{margin-top:10px}
.join{position:absolute;left:20px;top:266px;width:235px;display:flex;align-items:center;justify-content:center;gap:8px;font-family:"Oswald",sans-serif;font-weight:300;font-size:21px}
.join::before,.join::after{content:"";width:34px;height:1px;background:var(--white)}
.join-url{position:absolute;left:10px;top:298px;width:255px;text-align:center;font-size:8px}
.programs-title{position:absolute;left:297px;top:326px;font-family:"Oswald",sans-serif;font-weight:300;font-size:30px;letter-spacing:-0.5px}
.program-column{position:absolute;display:flex;flex-direction:column;gap:7px}
.program-column.left{left:297px;top:366px;width:220px}
.program-column.right{left:562px;top:306px;width:248px}
.program-head{display:flex;align-items:center;gap:6px;font-family:"Oswald",sans-serif;font-weight:300;font-size:18px;line-height:21px}
.program-icon{width:19px;height:19px;border-radius:50%;background:var(--white);position:relative;flex:none}
.program-icon::after{content:"";position:absolute;left:6px;top:6px;width:7px;height:7px;border-radius:50%;background:var(--blue)}
.program p{margin:3px 0 0 25px;font-size:7.2px;line-height:9.5px;color:var(--ink);text-align:justify;letter-spacing:-0.1px}

/* BACK */
.back{position:absolute;left:0;top:610px;width:824px;height:580px;overflow:hidden;font-family:"Open Sans",sans-serif;color:var(--white)}
.back-photo{position:absolute;inset:0;background:radial-gradient(ellipse at 55% 30%,#3a4550 0%,#1a2128 45%,#07090c 100%)}
.title-band{position:absolute;left:0;top:44px;width:824px;height:58px;background:var(--band);opacity:.95}
.title-text{position:absolute;left:151px;top:56px;font-weight:700;font-size:27px;line-height:34px;color:var(--blue)}
.title-text .accent{color:var(--pink)}
.avatar{position:absolute;left:13px;top:16px;width:114px;height:114px;border-radius:50%;border:4px solid var(--blue);background:radial-gradient(circle at 50% 45%,#5a8a4a,#2a3440 70%)}
.timetable{position:absolute;left:22px;top:143px;border-collapse:separate;border-spacing:1px 0;font-family:"Roboto Condensed",sans-serif;font-size:11px}
.timetable th,.timetable td{height:25px;text-align:center;white-space:nowrap;border-bottom:1px solid rgba(0,0,0,.25)}
.timetable th{background:var(--blue-light);font-family:"Open Sans",sans-serif;font-weight:400;font-size:11.5px;height:21px}
.timetable .time{width:56px;background:var(--blue-light);font-family:"Open Sans",sans-serif;font-size:12px;text-align:left;padding-left:8px}
.timetable .day{width:118px}
.timetable td{color:var(--ink);font-weight:700;letter-spacing:-0.2px}
.timetable tr:nth-child(odd) td:not(.time){background:var(--blue-cell)}
.timetable tr:nth-child(even) td:not(.time){background:var(--blue-light)}
.saturday{position:absolute;left:692px;top:143px;width:120px;font-family:"Roboto Condensed",sans-serif}
.saturday-head{height:21px;background:var(--pink);text-align:center;font-family:"Open Sans",sans-serif;font-size:11.5px;line-height:21px}
.sat-slot{height:42px;margin-top:4px;background:var(--blue-cell);text-align:center;color:var(--ink);font-size:11px;font-weight:700;padding-top:5px;line-height:15px}
.sat-slot .sat-time{display:block;color:var(--white);font-family:"Open Sans",sans-serif;font-weight:400;font-size:12px}
.tagline{position:absolute;left:56px;top:478px;font-size:19px;font-weight:400;letter-spacing:7px;color:var(--blue)}
.contact{position:absolute;left:40px;top:512px;width:500px;text-align:center;font-size:12.5px;line-height:17px}
.contact .web{color:var(--blue);font-weight:700}
.brand{position:absolute;left:572px;top:505px;width:215px;display:flex;align-items:center;gap:10px;font-family:"Open Sans",sans-serif;font-weight:700;font-size:20px;line-height:22px;color:var(--white)}
.brand-mark{width:16px;height:16px;background:var(--white);flex:none}
</style>
</head>
<body>
<div class="canvas">

  <section class="front">
    <svg class="front-shapes" width="824" height="580" viewBox="0 0 824 580">
      <polygon points="0,110 275,124 275,250 0,236" fill="#0b8ccd" opacity="0.55"/>
      <polygon points="275,0 824,0 824,274 275,320" fill="#2a2f36" role="img" aria-label="Photo of a group training class with kettlebells in the gym"/>
      <polygon points="0,342 275,320 275,580 0,580" fill="#6b5850" role="img" aria-label="Photo of a woman training on pads in the boxing ring"/>
      <polygon points="318,320 336,320 327,328" fill="#2a2f36"/>
    </svg>

    <h1 class="headline">NO EXPERIENCE?<br>NO PROBLEM!</h1>
    <div class="intro">
      <p>Riverstone Pulse Gym is a fun community of humble people.</p>
      <p>Our goal is to help guide you towards a fitter, healthier lifestyle!</p>
    </div>
    <div class="join">JOIN TODAY!</div>
    <div class="join-url">www.riverstonepulsegym-example.com/getting-started</div>

    <h2 class="programs-title">OUR PROGRAMS</h2>

    <div class="program-column left">
      <div class="program">
        <div class="program-head"><span class="program-icon"></span>HIIT</div>
        <p>High intensity interval training is 30-45 minutes of fat burning fun. The class is a mix of cardio, bodyweight and some resistance movements.</p>
      </div>
      <div class="program">
        <div class="program-head"><span class="program-icon"></span>CONDITIONING</div>
        <p>A full hour of strength, cardio and bodyweight training to get you in tip top shape. Expect a mix of barbells, kettlebells, rowing machines, bikes and other training methods.</p>
      </div>
      <div class="program">
        <div class="program-head"><span class="program-icon"></span>BWS</div>
        <p>This is our big Friday session to set you up for the weekend. 90 minutes of hard training that is done with a team emphasis. From heavy lifting to cardio triathlons, this class has it all but not for the faint hearted.</p>
      </div>
    </div>

    <div class="program-column right">
      <div class="program">
        <div class="program-head"><span class="program-icon"></span>MUAY THAI</div>
        <p>Commonly known as the science of 8 limbs you will learn how to punch, kick, knee and elbow. Thailands national sport is a great way to get your fitness kick. We train the complete beginner all the way to international fighters so you are in great hands.</p>
      </div>
      <div class="program">
        <div class="program-head"><span class="program-icon"></span>KIDS MUAY THAI</div>
        <p>Our junior program starts from age 6 onwards. Muay Thai is a great way for kids to get active and fit while learning new skills. Training in martial arts also teaches self discipline and socialisation skills.</p>
      </div>
      <div class="program">
        <div class="program-head"><span class="program-icon"></span>YOGA</div>
        <p>A combination of physical and mental practises that will leave you focused and refreshed for whatever the week throws at you. We always recommend our yoga classes as a great way to balance the high intensity training we offer.</p>
      </div>
      <div class="program">
        <div class="program-head"><span class="program-icon"></span>Q-PRESS</div>
        <p>Strength training with a little bit of conditioning. We regularly update the program and re test lifts to ensure you are making progress and getting stronger.</p>
      </div>
    </div>
  </section>

  <section class="back">
    <div class="back-photo" role="img" aria-label="Dark photo of a member training in the gym"></div>
    <div class="title-band"></div>
    <div class="avatar" role="img" aria-label="Photo of a trainer lifting a kettlebell"></div>
    <h2 class="title-text">Riverstone Pulse <span class="accent">timetable of classes</span></h2>

    <table class="timetable">
      <thead>
        <tr><th class="time"></th><th class="day">MONDAY</th><th class="day">TUESDAY</th><th class="day">WEDNESDAY</th><th class="day">THURSDAY</th><th class="day">FRIDAY</th></tr>
      </thead>
      <tbody>
        <tr><td class="time">06:00</td><td></td><td>Q-Press</td><td>Strength and Conditioning</td><td></td><td>Q-Press</td></tr>
        <tr><td class="time">07:00</td><td>Conditioning</td><td>Fight Camp Muay Thai</td><td>Yoga (5/25)</td><td>Conditioning</td><td>Fight Camp Muay Thai</td></tr>
        <tr><td class="time">08:00</td><td>Open Gym</td><td>Open Gym</td><td>Open Gym</td><td>Open Gym</td><td>Open Gym</td></tr>
        <tr><td class="time">10:00</td><td>Q-Press</td><td></td><td>Q-Press</td><td></td><td>Q-Press</td></tr>
        <tr><td class="time">12:10</td><td>Lunch time HIIT</td><td>Lunch time HIIT</td><td></td><td>Lunch time HIIT</td><td>Lunch time HIIT</td></tr>
        <tr><td class="time">16:00</td><td>Open Gym</td><td>Open Gym</td><td>Open Gym</td><td>Open Gym</td><td>Open Gym</td></tr>
        <tr><td class="time">17:00</td><td>Q-Press</td><td></td><td>Q-Press</td><td></td><td>Q-Press</td></tr>
        <tr><td class="time">17:15</td><td></td><td>HIIT (13/30)</td><td>HIIT (8/30)</td><td>Q-Press</td><td></td></tr>
        <tr><td class="time">18:00</td><td>Fundamentals</td><td>Conditioning</td><td>Fundamentals</td><td>Conditioning</td><td>BWS</td></tr>
        <tr><td class="time">18:00</td><td>Muay Thai Foundations</td><td>Kids</td><td>Muay Thai Foundations</td><td>Kids</td><td></td></tr>
        <tr><td class="time">19:00</td><td>Strength and Conditioning</td><td>Muay Thai Intermediate</td><td></td><td>Muay Thai Intermediate</td><td></td></tr>
        <tr><td class="time">19:15</td><td></td><td></td><td>Yoga (5/25)</td><td></td><td></td></tr>
      </tbody>
    </table>

    <div class="saturday">
      <div class="saturday-head">SATURDAY</div>
      <div class="sat-slot"><span class="sat-time">10:00</span>Saturday Circuit</div>
      <div class="sat-slot"><span class="sat-time">11:00</span>Open Gym</div>
      <div class="sat-slot"><span class="sat-time">11:00</span>Fundamentals</div>
      <div class="sat-slot"><span class="sat-time">11:00</span>Kids</div>
      <div class="sat-slot"><span class="sat-time">12:00</span>Muay Thai Foundations</div>
    </div>

    <div class="tagline">MAKE CHANGES, NOT EXCUSES</div>
    <div class="contact">
      Tel. 07930625184 &nbsp;| Email: info@riverstonepulsegym-example.com<br>
      Riverstone Pulse Gym, Unit 27C, 214 Kelvane Road, Marrow Heath, Glasgow, G72QT<br>
      <span class="web">www.riverstonepulsegym-example.com</span>
    </div>
    <div class="brand"><span class="brand-mark"></span>RIVERSTONE PULSE GYM</div>
  </section>

</div>
</body>
</html>
```